Visit card

Industry/Entity Type

Health Care

Contact Information for Business Card

O VITALIS SYSTEMS
Odile Brevard - chef de Projet

Requirements
Must have
• 318 Gaston Lemaire Street 59710 LORVANCE Tel: 33 (0) 327 481 605 Mobile: 06 42 19 37 64 Web: www.quorvexsystems.example Contact: o.brevard@o-vitalissystems.example
Should not have
• Respect for color

```html
<!DOCTYPE html>
<html lang="fr">
<head>
<meta charset="utf-8">
<title>O Vitalis Systems – Carte de visite</title>
<link rel="stylesheet" href="https://fonts.googleapis.com/css2?family=Montserrat:wght@500;600;700&family=Lato:wght@400;700&display=swap">
<style>
  :root {
    --stage: #6f6f71;
    --card-dark: #3a3a3c;
    --card-light: #ffffff;
    --brand-red: #e3202a;
    --ink: #2f2f31;
    --rule: #4a4a4c;
    --band-dark: #3d3d3f;
  }
  * { box-sizing: border-box; margin: 0; padding: 0; }
  html, body { width: 1200px; height: 895px; overflow: hidden; }
  body {
    background: var(--stage);
    font-family: "Lato", Arial, sans-serif;
    color: var(--ink);
    position: relative;
  }
  .card {
    position: absolute;
    top: 293px;
    width: 540px;
    height: 309px;
    border-radius: 16px;
    overflow: hidden;
  }
  .card--back { left: 30px; background: var(--card-dark); }
  .card--front { left: 630px; background: var(--card-light); }

  .brand {
    position: absolute;
    display: flex;
    align-items: center;
    gap: 12px;
    font-family: "Montserrat", Arial, sans-serif;
    font-weight: 700;
    color: var(--brand-red);
    letter-spacing: 1px;
    white-space: nowrap;
  }
  .brand__dot {
    border-radius: 50%;
    background: var(--brand-red);
    flex: none;
  }
  .card--back .brand { left: 50%; top: 50%; transform: translate(-50%, -50%); font-size: 30px; gap: 18px; }
  .card--back .brand__dot { width: 66px; height: 66px; }
  .card--front .brand { right: 34px; top: 50px; font-size: 18px; }
  .card--front .brand__dot { width: 36px; height: 36px; }

  .divider {
    position: absolute;
    left: 220px; right: 34px; top: 132px;
    height: 1px; background: var(--rule);
  }
  .person { position: absolute; left: 34px; top: 112px; }
  .person__name {
    font-family: "Montserrat", Arial, sans-serif;
    font-weight: 600;
    color: var(--brand-red);
    font-size: 19px;
    text-transform: uppercase;
    letter-spacing: 0.3px;
  }
  .person__role { font-size: 13px; margin-top: 1px; }

  .contacts { position: absolute; left: 34px; top: 168px; list-style: none; }
  .contacts li { display: flex; align-items: center; gap: 8px; font-size: 12.5px; line-height: 19px; }
  .contacts svg { width: 13px; height: 13px; flex: none; }

  .address {
    position: absolute; right: 34px; top: 196px;
    text-align: right; font-size: 12.5px; line-height: 16px;
  }

  .tab { position: absolute; left: 0; top: 196px; width: 14px; height: 24px; background: var(--band-dark); }
  .band-dark { position: absolute; left: 0; bottom: 0; width: 390px; height: 18px; background: var(--band-dark); }
  .band-red { position: absolute; left: 396px; right: 0; bottom: 0; height: 42px; background: var(--brand-red); }
</style>
</head>
<body>

  <section class="card card--back" aria-label="Verso de la carte">
    <div class="brand"><span class="brand__dot"></span>O VITALIS SYSTEMS</div>
  </section>

  <section class="card card--front" aria-label="Recto de la carte">
    <div class="brand"><span class="brand__dot"></span>O VITALIS SYSTEMS</div>
    <div class="divider"></div>

    <div class="person">
      <p class="person__name">Odile Brevard</p>
      <p class="person__role">Chef de Projet</p>
    </div>

    <ul class="contacts">
      <li>
        <svg viewBox="0 0 14 14" aria-hidden="true"><circle cx="7" cy="7" r="7" fill="#e3202a"/><rect x="4.6" y="3" width="4.8" height="8" rx="1" fill="none" stroke="#fff" stroke-width="1.1"/></svg>
        06 42 19 37 64
      </li>
      <li>
        <svg viewBox="0 0 14 14" aria-hidden="true"><circle cx="7" cy="7" r="7" fill="#e3202a"/><path d="M4.3 4.2c.4-.5 1-.5 1.3 0l.6 1c.2.4 0 .7-.3 1 .4.9 1 1.5 1.9 1.9.3-.3.6-.5 1-.3l1 .6c.5.3.5.9 0 1.3-2.2 1.4-6.9-3.3-5.5-5.5z" fill="#fff"/></svg>
        +33 (0) 327 481 605
      </li>
      <li>
        <svg viewBox="0 0 14 14" aria-hidden="true"><circle cx="7" cy="7" r="7" fill="#e3202a"/><rect x="3.5" y="4.5" width="7" height="5" fill="none" stroke="#fff" stroke-width="1"/><path d="M3.5 4.5 7 7.3l3.5-2.8" fill="none" stroke="#fff" stroke-width="1"/></svg>
        o.brevard@o-vitalissystems.example
      </li>
      <li>
        <svg viewBox="0 0 14 14" aria-hidden="true"><circle cx="7" cy="7" r="7" fill="#e3202a"/><circle cx="7" cy="7" r="3.8" fill="none" stroke="#fff" stroke-width="0.9"/><path d="M3.2 7h7.6M7 3.2v7.6" stroke="#fff" stroke-width="0.8"/></svg>
        www.quorvexsystems.example
      </li>
    </ul>

    <p class="address">318 Rue Gaston Lemaire<br>59710 LORVANCE</p>

    <div class="tab"></div>
    <div class="band-dark"></div>
    <div class="band-red"></div>
  </section>

</body>
</html>
```